Assessment Report cover design and formatting

This report is for senior executives and provides leaders with detailed insight into their capabilities and skills. The cover should have space for the date and name of the person doing the assessment. We are looking to modernise the report cover design. We would like the report to be our company colours if possible. The work will likely expand once the cover is done to other parts of the report, ie. the format and layout of the report etc.

Company colours:
Primary colours:
• Blue #0D47A1, #115CD0, #90B6ED, #EEf3FB
• Green #0D91A1, #47A10D, #324C196, #0DA11D
Additional colours:
• Purple #A10D91
• Brown #A1670D
• Red #A10D47

Target Market(s)

Executives

Industry/Entity Type

Consulting, leadership development

Colors
0094D4
00A9DD
6FCCEA
C7EBF8
E9F6FB
00AB8E
00BBA5
67D7C9
C6EFE9
E9F9F6
E54698
E96AAD
F1A4CE
F9D9EA
FCEFF6
6B429C
8869AF
B7A5CE
E3DAEB
F3F0F8

Requirements
Must have
• The report cover should have space for name of user, the date and company logo. Cover should be in A4 size.

```html
<!DOCTYPE html>
<html lang="en">
<head>
<meta charset="utf-8">
<title>Growth Leader Assessment – Insight Report Cover</title>
<link rel="stylesheet" href="https://fonts.googleapis.com/css2?family=Montserrat:wght@400;500;600;800;900&display=swap">
<style>
  :root {
    --stage: #7f7f7f;
    --paper: #eeeeee;
    --navy: #1f3fa6;
    --royal: #1a56c4;
    --sky: #1e8fd8;
    --aqua: #22c1cf;
    --teal: #2fb8a0;
    --green: #3fbf7a;
    --ink: #2a2a2a;
    --white: #ffffff;
  }
  * { box-sizing: border-box; margin: 0; padding: 0; }
  html, body { width: 1200px; height: 840px; overflow: hidden; }
  body {
    background: var(--stage);
    font-family: "Montserrat", Arial, sans-serif;
    display: flex; align-items: center; justify-content: center;
  }
  .report-cover {
    position: relative;
    width: 552px; height: 780px;
    background: var(--paper);
    overflow: hidden;
    box-shadow: 0 10px 30px rgba(0,0,0,.25);
  }
  .cover-photo {
    position: absolute; inset: 0 0 240px 0;
    background:
      radial-gradient(ellipse at 80% 30%, rgba(30,80,200,.55), transparent 60%),
      linear-gradient(200deg, #1d4fc2 0%, #1a7fd6 35%, #1fa6d6 55%, #2cc0b0 80%, #3ec79a 100%);
  }
  .cover-shapes { position: absolute; inset: 0; }
  .cover-title {
    position: absolute; left: 70px; top: 160px;
    color: var(--white); text-transform: uppercase;
  }
  .cover-title .kicker { font-weight: 500; font-size: 30px; letter-spacing: 1px; line-height: 1; }
  .cover-title .main { font-weight: 900; font-size: 58px; line-height: .95; letter-spacing: 1px; }
  .cover-title .main.wide { font-size: 52px; }
  .cover-title .rule { width: 210px; height: 3px; background: var(--white); margin-top: 18px; }
  .brand {
    position: absolute; left: 30px; top: 565px;
    color: var(--royal);
  }
  .brand-name { font-weight: 600; font-size: 22px; letter-spacing: 1px; display: flex; align-items: center; gap: 8px; }
  .brand-mark { width: 12px; height: 12px; border-radius: 50%; background: var(--royal); }
  .brand-tagline { font-weight: 600; font-size: 11px; letter-spacing: 3px; margin-top: 6px; padding-left: 20px; }
  .report-for {
    position: absolute; right: 36px; top: 590px; text-align: right;
  }
  .report-for .insight { color: var(--green); font-weight: 500; font-size: 30px; letter-spacing: 1px; line-height: 1; }
  .report-for .heading { color: var(--royal); font-weight: 900; font-size: 32px; line-height: 1.05; }
  .report-for .subject, .report-for .date { color: var(--royal); font-size: 15px; line-height: 1.3; }
  .report-for .subject { margin-top: 6px; }
  .sign-fields { position: absolute; left: 90px; right: 36px; top: 712px; font-size: 10px; color: var(--ink); }
  .field { display: flex; align-items: flex-end; gap: 8px; margin-bottom: 14px; }
  .field .line { flex: 1; border-bottom: 1px solid var(--ink); height: 1px; }
</style>
</head>
<body>
  <main class="report-cover">
    <div class="cover-photo" role="img" aria-label="Photograph of business professionals working with growth charts, tinted blue to teal"></div>

    <svg class="cover-shapes" viewBox="0 0 552 780" width="552" height="780" aria-hidden="true">
      <defs>
        <linearGradient id="bandGradient" x1="0" y1="0" x2="1" y2="0">
          <stop offset="0" stop-color="#1a56c4"/>
          <stop offset=".6" stop-color="#1e8fd8"/>
          <stop offset=".8" stop-color="#22c1cf"/>
          <stop offset="1" stop-color="#3fbf7a"/>
        </linearGradient>
      </defs>
      <polygon class="lower-panel" fill="#eeeeee"
        points="0,492 62,470 150,474 215,512 300,508 362,542 440,534 552,478 552,780 0,780"/>
      <polyline class="growth-band-shadow" fill="none" stroke="#1f3fa6" stroke-width="26" stroke-linejoin="miter"
        points="-10,470 60,446 150,450 215,488 300,484 360,518 440,510 515,468"/>
      <polyline class="growth-band" fill="none" stroke="url(#bandGradient)" stroke-width="14" stroke-linejoin="miter"
        points="-10,478 60,456 150,460 215,498 300,494 360,528 440,520 515,478"/>
      <polygon class="growth-arrowhead" fill="#3fbf7a" points="495,455 552,440 540,497"/>
    </svg>

    <header class="cover-title">
      <div class="kicker">Growth</div>
      <div class="main">Leader</div>
      <div class="main wide">Assessment</div>
      <div class="rule"></div>
    </header>

    <div class="brand">
      <div class="brand-name"><span class="brand-mark"></span>Northbeam Partners</div>
      <div class="brand-tagline">Leadership Advisors</div>
    </div>

    <section class="report-for">
      <div class="insight">INSIGHT</div>
      <div class="heading">REPORT FOR:</div>
      <div class="subject">Sample</div>
      <div class="date">22 August 2023</div>
    </section>

    <section class="sign-fields">
      <div class="field"><span>Name:</span><span class="line"></span></div>
      <div class="field"><span>Date:</span><span class="line"></span></div>
    </section>
  </main>
</body>
</html>
```